Boutique Store Selling Antiques and Unique Finds

I need a Web Page designed for my Store Called "Willow Lane". I would like a very classic, muted design that looks European when pulled up. I will be selling Antiques from all over the world and Unique finds that have reproduced. I will also be selling high-end purses and jewelry with unique, reasonable products for the every-day buyer as well.

Target Market(s)

25-70 year old men and women;)

Coding

Coded - Design and coding required

Number of Pages Required

1 page

Colors

Designer to choose only greyscale colors for use in the design.

Requirements
Must have
• I want it

```html
<!DOCTYPE html>
<html lang="en">
<head>
<meta charset="utf-8">
<title>Willow Lane — Antiques &amp; Unique Finds</title>
<link href="https://fonts.googleapis.com/css2?family=Cinzel:wght@600;700&family=Open+Sans:wght@400;600;700&display=swap" rel="stylesheet">
<style>
:root{
  --ink:#1f1f1f;
  --dark:#232323;
  --text:#3a3a3a;
  --muted:#6b6b6b;
  --line:#d9d9d9;
  --paper:#ffffff;
  --band:#f3f3f3;
  --footer-text:#e6e6e6;
  --display:"Cinzel",serif;
  --body:"Open Sans",sans-serif;
}
*{box-sizing:border-box;margin:0;padding:0}
html,body{width:1200px;height:3440px;overflow:hidden;background:var(--paper);font-family:var(--body);color:var(--text)}
.page{position:relative;width:1200px;height:3440px}
.abs{position:absolute}

/* top bar */
.topbar{left:0;top:0;width:1200px;height:38px;background:var(--dark);color:#fff;font-size:11.5px;font-weight:600;display:flex;align-items:center;justify-content:space-between;padding:0 111px}
.topbar .right{display:flex;gap:12px;align-items:center}

/* header */
.header{left:0;top:38px;width:1200px;height:80px;display:flex;align-items:center;padding:0 111px;justify-content:space-between}
.brand{font-family:var(--display);font-weight:700;font-size:24px;letter-spacing:2px;color:var(--ink)}
.nav{display:flex;align-items:center;gap:23px;font-size:15px;color:var(--ink)}
.nav .active{border-bottom:2px solid var(--ink);padding:6px 0}
.nav .caret{font-size:10px;margin-left:5px;color:var(--muted)}
.nav .sep{color:var(--ink)}

/* hero */
.hero{left:0;top:118px;width:1200px;height:600px;background:radial-gradient(ellipse at 55% 55%,#b9a27f 0%,#6e5a43 35%,#3b2f28 70%,#1d1917 100%)}
.hero-box{left:322px;top:310px;width:556px;height:216px;background:rgba(210,205,200,.55);padding:8px}
.hero-box .frame{border:1px solid rgba(60,60,60,.6);height:100%;text-align:center;padding-top:14px}
.hero-box h1{font-family:var(--display);font-size:34px;letter-spacing:2px;color:var(--ink)}
.hero-box p{font-size:16px;line-height:26px;color:var(--ink);margin:6px 30px 0}
.btn-dark{display:inline-block;background:var(--ink);color:#fff;font-weight:700;font-size:14.5px;padding:11px 20px}
.hero-box .btn-dark{margin-top:16px}
.arrow{width:36px;height:36px;background:rgba(20,20,20,.75);display:flex;align-items:center;justify-content:center;top:400px}

/* section titles */
.section-title{left:0;width:1200px;text-align:center;font-family:var(--display);font-size:32px;font-weight:700;letter-spacing:2px;color:var(--ink)}

/* cards */
.card{background:#fff;box-shadow:0 0 6px rgba(0,0,0,.14);text-align:center}
.card .photo{margin:9px 9px 0}
.card .name{font-size:19px;color:var(--ink);margin-top:10px;letter-spacing:.5px}
.card .price{font-size:16px;color:var(--muted);margin-top:4px}
.card .actions{display:flex;justify-content:center;gap:13px;margin-top:12px}
.btn-outline{border:2px solid var(--ink);font-size:14px;font-weight:600;color:var(--ink);padding:0 12px;height:40px;line-height:36px}
.btn-cart{width:42px;height:40px;background:var(--ink);display:flex;align-items:center;justify-content:center}
.dots{left:0;top:1272px;width:1200px;display:flex;justify-content:center;gap:6px}
.dots span{width:12px;height:12px;border:1.5px solid var(--ink)}
.dots .on{background:var(--ink)}

/* best seller */
.best{left:0;top:1362px;width:1200px;height:344px;background:var(--band)}
.best .photo{position:absolute;left:0;top:0;width:650px;height:344px;background:linear-gradient(90deg,#d8d2c6 0%,#a88d64 35%,#8a7254 55%,#c9c2b5 85%,#f3f3f3 100%)}
.best .copy{position:absolute;left:649px;top:84px;width:440px}
.best h2{font-family:var(--display);font-size:42px;letter-spacing:2px;color:var(--ink)}
.best p{font-size:15px;line-height:22px;margin-top:10px;color:var(--text)}
.best .btn-dark{margin-top:22px;padding:12px 20px}

/* shop online */
.intro{left:150px;width:900px;text-align:center;font-size:15px;line-height:22px;color:var(--muted)}
.intro strong{font-weight:400;color:var(--ink)}
.quick{left:287px;top:2110px;background:rgba(225,225,225,.9);font-size:15px;font-weight:600;color:var(--ink);padding:10px 17px}
.pager{left:453px;top:2824px;display:flex;border:1px solid #cfcfcf}
.pager span{width:37px;height:37px;display:flex;align-items:center;justify-content:center;font-family:var(--display);font-weight:700;font-size:16px;color:var(--ink);border-left:1px solid #cfcfcf}
.pager span:first-child{border-left:none}
.pager .on{background:var(--ink);color:#fff}

/* footer */
.footer{left:0;top:2948px;width:1200px;height:492px;background:var(--dark);color:var(--footer-text)}
.footer h3{font-family:var(--display);font-size:22px;letter-spacing:1.5px;color:#fff;text-align:center;position:absolute;left:0;top:30px;width:1200px}
.footer .sub{position:absolute;left:0;top:68px;width:1200px;text-align:center;font-size:15px}
.signup{position:absolute;left:284px;top:122px;width:632px;height:42px;background:#fff;display:flex;align-items:center;justify-content:space-between;padding:0 3px 0 15px}
.signup span{font-size:14px;color:#8a8a8a}
.signup .submit{background:var(--ink);color:#fff;font-weight:700;font-size:14.5px;height:34px;line-height:34px;padding:0 20px}
.rule{position:absolute;left:111px;width:978px;height:1px;background:#555}
.fbrand{position:absolute;left:111px;top:250px;font-family:var(--display);font-weight:700;font-size:22px;letter-spacing:2px;color:#fff}
.socials{position:absolute;left:134px;top:315px;display:flex;gap:8px}
.socials span{width:35px;height:35px;background:#3e3e3e;display:flex;align-items:center;justify-content:center}
.socials i{width:10px;height:10px;border-radius:50%;background:#d8d8d8;display:block}
.fcol{position:absolute;top:232px;font-size:15px;line-height:24px}
.fcol h4{font-size:19px;font-weight:600;color:#fff;margin-bottom:12px}
.contact-row{display:flex;gap:18px;align-items:flex-start;margin-bottom:8px}
.contact-row svg{margin-top:6px;flex:none}
.copy-line{position:absolute;left:111px;top:446px;font-size:12.5px}
.copy-line b{font-family:var(--display);letter-spacing:1px}
.cards{position:absolute;left:781px;top:436px;display:flex;gap:6px}
.cards span{width:54px;height:31px;background:#d6d6d6;border-radius:3px}
.cards span:nth-child(2){background:#f2f2f2}
.cards span:nth-child(3){background:#8d8d8d}
.cards span:nth-child(4){background:#b9b9b9}
.cards span:nth-child(5){background:#9f9f9f}
.tiny{position:absolute;left:1133px;top:448px;font-size:11px}
</style>
</head>
<body>
<div class="page">

  <div class="abs topbar">
    <div>GET 20% OFF YOUR FIRST ORDER SIGN UP &nbsp;| &nbsp;FREE SHIPPING ON DOMESTIC ORDERS OVER $40</div>
    <div class="right"><span>REGISTER</span><span>SIGN IN</span><span>&nbsp;|&nbsp;</span>
      <span><svg width="13" height="11" viewBox="0 0 13 11"><path d="M0 1h2.5l1.6 6h7l1.4-4.5H3.3" fill="none" stroke="#fff" stroke-width="1.6"/><circle cx="5" cy="9.5" r="1.1" fill="#fff"/><circle cx="10" cy="9.5" r="1.1" fill="#fff"/></svg>(0)</span></div>
  </div>

  <header class="abs header">
    <div class="brand">Willow Lane</div>
    <nav class="nav">
      <span class="active">Home</span>
      <span>Shop Online</span>
      <span>Our Collections<span class="caret">&#9013;</span></span>
      <span>New arrivals</span>
      <span>Sale<span class="caret">&#9013;</span></span>
      <span>Events</span>
      <span>Contact Us</span>
      <span class="sep">|</span>
      <svg width="14" height="14" viewBox="0 0 14 14"><circle cx="6" cy="6" r="4.3" fill="none" stroke="#1f1f1f" stroke-width="2"/><path d="M9.2 9.2L13 13" stroke="#1f1f1f" stroke-width="2.2"/></svg>
    </nav>
  </header>

  <section class="abs hero" role="img" aria-label="Antique pocket watch resting on old leather-bound books and a map"></section>
  <div class="abs arrow" style="left:39px"><svg width="12" height="14" viewBox="0 0 12 14"><path d="M8 2L3 7l5 5" fill="none" stroke="#fff" stroke-width="2"/></svg></div>
  <div class="abs arrow" style="left:1127px"><svg width="12" height="14" viewBox="0 0 12 14"><path d="M4 2l5 5-5 5" fill="none" stroke="#fff" stroke-width="2"/></svg></div>
  <div class="abs hero-box"><div class="frame">
    <h1>Willow Lane</h1>
    <p>Lorem ipsum dolor sit amet, consectetur adipiscing elit, sed do eiusmod tempor incididu.</p>
    <span class="btn-dark">SHOP NOW</span>
  </div></div>

  <h2 class="abs section-title" style="top:790px">Our Collections</h2>

  <div class="abs card" style="left:111px;top:864px;width:308px;height:362px">
    <div class="photo" role="img" aria-label="Gilded star crown on stacked antique books" style="height:223px;background:linear-gradient(160deg,#e8e2d6,#a68c5c 50%,#5a3a2c)"></div>
    <div class="name">PRODUCT TITTLE</div><div class="price">$3555.00</div>
    <div class="actions"><span class="btn-outline">SHOP NOW</span><span class="btn-cart"><svg width="16" height="14" viewBox="0 0 13 11"><path d="M0 1h2.5l1.6 6h7l1.4-4.5H3.3" fill="#fff" stroke="#fff" stroke-width="1.4"/><circle cx="5" cy="9.5" r="1.1" fill="#fff"/><circle cx="10" cy="9.5" r="1.1" fill="#fff"/></svg></span></div>
  </div>
  <div class="abs card" style="left:446px;top:864px;width:308px;height:362px">
    <div class="photo" role="img" aria-label="Jewelled bronze crown on a pale backdrop" style="height:223px;background:linear-gradient(170deg,#d9d3c6,#8a7150 55%,#4a3a2c)"></div>
    <div class="name">PRODUCT TITTLE</div><div class="price">$3555.00</div>
    <div class="actions"><span class="btn-outline">SHOP NOW</span><span class="btn-cart"><svg width="16" height="14" viewBox="0 0 13 11"><path d="M0 1h2.5l1.6 6h7l1.4-4.5H3.3" fill="#fff" stroke="#fff" stroke-width="1.4"/><circle cx="5" cy="9.5" r="1.1" fill="#fff"/><circle cx="10" cy="9.5" r="1.1" fill="#fff"/></svg></span></div>
  </div>
  <div class="abs card" style="left:781px;top:864px;width:308px;height:362px">
    <div class="photo" role="img" aria-label="Gold crown with red stones on black velvet" style="height:223px;background:radial-gradient(ellipse at 50% 65%,#c9a04a,#5a4320 40%,#0d0d0d 75%)"></div>
    <div class="name">PRODUCT TITTLE</div><div class="price">$3555.00</div>
    <div class="actions"><span class="btn-outline">SHOP NOW</span><span class="btn-cart"><svg width="16" height="14" viewBox="0 0 13 11"><path d="M0 1h2.5l1.6 6h7l1.4-4.5H3.3" fill="#fff" stroke="#fff" stroke-width="1.4"/><circle cx="5" cy="9.5" r="1.1" fill="#fff"/><circle cx="10" cy="9.5" r="1.1" fill="#fff"/></svg></span></div>
  </div>
  <div class="abs dots"><span></span><span class="on"></span><span></span><span></span></div>

  <section class="abs best">
    <div class="photo" role="img" aria-label="Ornate bronze crown set with blue stones"></div>
    <div class="copy">
      <h2>Best Seller</h2>
      <p>Lorem ipsum dolor sit amet, consectetur adipiscing elit, sed do eiusmod tempor incididunt ut labore.</p>
      <span class="btn-dark">SHOP NOW</span>
    </div>
  </section>

  <h2 class="abs section-title" style="top:1782px;font-size:30px">SHOP ONLINE</h2>
  <p class="abs intro" style="top:1832px">Sed ut perspiciatis unde omnis iste natus error sit voluptatem accusantium doloremque laudantium, totam rem aperiam, eaque ipsa quae ab illo inventore veritatis et quasi architec</p>
  <p class="abs intro" style="top:1888px;color:var(--text)">For all enquiries please email <strong>shop.antiques@willowlane.com</strong></p>

  <div class="abs card" style="left:111px;top:1940px;width:475px;height:470px">
    <div class="photo" role="img" aria-label="Pocket watch on an old wooden chest with compasses" style="height:375px;background:linear-gradient(150deg,#6a4a40,#4a2f2a 45%,#8b8a85 75%,#3c2622)"></div>
    <div class="name" style="margin-top:14px">PRODUCT TITTLE</div><div class="price">$3485.00</div>
  </div>
  <div class="abs quick">QUICK VIEW</div>
  <div class="abs card" style="left:613px;top:1940px;width:476px;height:470px">
    <div class="photo" role="img" aria-label="Blue and white porcelain vases" style="height:375px;background:linear-gradient(160deg,#1c2440,#3c4d7a 40%,#a88a64 60%,#20253a)"></div>
    <div class="name" style="margin-top:14px">PRODUCT TITTLE</div><div class="price">$3485.00</div>
  </div>

  <div class="abs card" style="left:111px;top:2448px;width:308px;height:310px">
    <div class="photo" role="img" aria-label="Engraved silver coffee set" style="height:222px;background:linear-gradient(160deg,#b7a898,#6b5a4d 50%,#3a2e28)"></div>
    <div class="name">PRODUCT TITTLE</div><div class="price">$3555.00</div>
  </div>
  <div class="abs card" style="left:446px;top:2448px;width:308px;height:310px">
    <div class="photo" role="img" aria-label="Brass carriage clock on a dark table" style="height:222px;background:radial-gradient(ellipse at 40% 50%,#a8884c,#4a3018 45%,#1a0f0a 85%)"></div>
    <div class="name">PRODUCT TITTLE</div><div class="price">$3555.00</div>
  </div>
  <div class="abs card" style="left:781px;top:2448px;width:308px;height:310px">
    <div class="photo" role="img" aria-label="Hourglass and globe over an old chart" style="height:222px;background:linear-gradient(150deg,#7a6448,#4a3a2a 50%,#a08664)"></div>
    <div class="name">PRODUCT TITTLE</div><div class="price">$3555.00</div>
  </div>

  <div class="abs pager"><span>1</span><span class="on">2</span><span>3</span><span>4</span><span>5</span><span>6</span><span>7</span><span>8</span></div>

  <footer class="abs footer">
    <h3>Join Our Mailing For Discounts</h3>
    <div class="sub">Sign up to receive the latest news and updates</div>
    <div class="signup"><span>Enter Email Address</span><span class="submit">SUBMIT</span></div>
    <div class="rule" style="top:197px"></div>

    <div class="fbrand">Willow Lane</div>
    <div class="socials"><span><i></i></span><span><i></i></span><span><i></i></span><span><i></i></span></div>

    <div class="fcol" style="left:415px"><h4>Shop</h4>Sale<br>Antique Vintage<br>Events<br>Gift<br>New Arrivals</div>
    <div class="fcol" style="left:625px"><h4>Terms Of Use</h4>Terms and Conditions<br>Privacy Policy<br>Site map</div>
    <div class="fcol" style="left:883px"><h4>Contact Us</h4>
      <div class="contact-row"><svg width="10" height="13" viewBox="0 0 10 13"><path d="M5 13S0 7.5 0 4.8a5 5 0 0110 0C10 7.5 5 13 5 13z" fill="#8f8f8f"/><circle cx="5" cy="4.8" r="1.8" fill="#232323"/></svg><span>1254 Harbor Row<br>United States</span></div>
      <div class="contact-row"><svg width="12" height="12" viewBox="0 0 12 12"><path d="M2.5 0l2 3-1.3 1.3a7 7 0 004.5 4.5L9 7.5l3 2-1.5 2.5C5 12 0 7 0 1.5z" fill="#8f8f8f"/></svg><span>(555) 214 7730</span></div>
      <div class="contact-row"><svg width="13" height="10" viewBox="0 0 13 10"><rect width="13" height="10" fill="#8f8f8f"/><path d="M0 0l6.5 5.5L13 0" fill="none" stroke="#232323" stroke-width="1.2"/></svg><span>hello@willowlane.com</span></div>
    </div>

    <div class="rule" style="top:423px"></div>
    <div class="copy-line">© Copyrights 2021 <b>WILLOW LANE</b>. All rights Reserved</div>
    <div class="cards"><span></span><span></span><span></span><span></span><span></span></div>
    <div class="tiny">C45</div>
  </footer>
</div>
</body>
</html>
```